Diverse, up-scale salon needs eye-catching, unique business cards.

We are looking for a unique business card design for our stylist but that can also be multi functional and used for appointment reminder and referrals. I will need a design in a format that I can modify names and titles going forward. In the past we have had a dark background with the logo on one side, and stylist and contact information on the other but we are open to all ideas. I have included our mission statement as well as branded colors below. The statement doesn't need to go on the card, it's just a reference for target market. We need space for the stylists name, title, instagram handle and then the salons phone number, website and address. I am also open to adding a spot for a qr code linked to the stylist instagram or the salon booking link.

primary brand colors:
#333333 #233415 #36502a #93874a #000000
Mission statement:
Vessolin Hair Studio, a high-end salon located in the lively Downtown Farmington, Michigan, is committed to providing exceptional services in a welcoming and relaxed environment to meet the needs of our diverse clientele.
Our salon specializes in contemporary custom haircuts, coloring, extensions, and barbering and beard grooming services. Our team of skilled stylists is passionate and inventive in their hair styling techniques. At the heart of our salon are values centered on quality, innovation, creativity, and above all, comfort. These core values are evident in every appointment across our customizable array of services.
Our goal is to establish a benchmark for exceptional hair care for every human.
Website: www.vessolinhairstudio.example
instagram: @vessolinhairstudio
address: 41782 Pelham Crest Rd, Larkmoor OH
phone: 555-613-4087

Industry/Entity Type

Hair Salon

Contact Information for Business Card

Stylist name, title, phone, instagram, website, address, (optional qr code)

Requirements
Should not have
• Does not need mission statement on the card.

```html
<!DOCTYPE html>
<html lang="en">
<head>
<meta charset="UTF-8">
<title>Vessolin Hair Studio — Stylist Business Card</title>
<link rel="stylesheet" href="https://fonts.googleapis.com/css2?family=Montserrat:wght@400;500;600&display=swap">
<style>
  :root {
    --canvas: #1e1e1e;
    --card: #333333;
    --ink: #e9e9e9;
    --ink-soft: #c4c4c4;
    --rule: #bdbdbd;
  }
  * { box-sizing: border-box; margin: 0; padding: 0; }
  html, body {
    width: 826px; height: 1200px; overflow: hidden;
    background: var(--canvas);
    font-family: "Montserrat", Arial, sans-serif;
    color: var(--ink);
  }
  .canvas { position: relative; width: 826px; height: 1200px; }
  .card {
    position: absolute; left: 132px;
    width: 561px; height: 320px;
    background: var(--card);
  }
  .card--front { top: 254px; display: flex; align-items: center; justify-content: center; }
  .card--back { top: 627px; }

  .brand { display: flex; align-items: center; gap: 18px; }
  .brand__ring {
    width: 58px; height: 58px; border-radius: 50%;
    border: 2px solid var(--ink); flex: none;
  }
  .brand__name {
    font-weight: 500; font-size: 24px; letter-spacing: 3px;
    text-transform: uppercase; color: var(--ink);
  }

  .back-brand {
    position: absolute; left: 18px; top: 0; width: 172px; height: 320px;
    display: flex; flex-direction: column; align-items: center; justify-content: center;
    gap: 14px; text-align: center;
  }
  .back-brand .brand__ring { width: 46px; height: 46px; }
  .back-brand .brand__name { font-size: 15px; letter-spacing: 2px; line-height: 1.5; }

  .divider {
    position: absolute; left: 203px; top: 87px;
    width: 1.5px; height: 148px; background: var(--rule);
  }
  .details { position: absolute; left: 228px; top: 82px; right: 16px; }
  .details__name { font-weight: 600; font-size: 19px; letter-spacing: 0.3px; line-height: 1.2; }
  .details__title { font-size: 14px; color: var(--ink-soft); margin-top: 1px; }
  .contact { list-style: none; margin-top: 14px; }
  .contact li {
    display: flex; align-items: center; gap: 8px;
    font-size: 14.5px; color: var(--ink-soft); height: 22px;
  }
  .contact svg { width: 13px; height: 13px; flex: none; }
  .contact__dot { width: 11px; height: 11px; border-radius: 50%; border: 1.5px solid var(--ink-soft); margin: 0 1px; flex: none; }
  .address { font-size: 15px; color: var(--ink-soft); margin-top: 7px; }
</style>
</head>
<body>
<main class="canvas">
  <section class="card card--front" aria-label="Card front">
    <div class="brand">
      <span class="brand__ring"></span>
      <span class="brand__name">Vessolin Hair Studio</span>
    </div>
  </section>

  <section class="card card--back" aria-label="Card back">
    <div class="back-brand">
      <span class="brand__ring"></span>
      <span class="brand__name">Vessolin<br>Hair Studio</span>
    </div>
    <span class="divider"></span>
    <div class="details">
      <h1 class="details__name">STYLIST NAME</h1>
      <p class="details__title">Designation</p>
      <ul class="contact">
        <li>
          <svg viewBox="0 0 24 24" aria-hidden="true"><path fill="#c4c4c4" d="M6.6 10.8a15.1 15.1 0 0 0 6.6 6.6l2.2-2.2a1 1 0 0 1 1-.25 11.4 11.4 0 0 0 3.6.57 1 1 0 0 1 1 1V20a1 1 0 0 1-1 1A17 17 0 0 1 3 4a1 1 0 0 1 1-1h3.5a1 1 0 0 1 1 1c0 1.25.2 2.45.57 3.57a1 1 0 0 1-.25 1z"/></svg>
          555-613-4087
        </li>
        <li>
          <svg viewBox="0 0 24 24" aria-hidden="true" fill="none" stroke="#c4c4c4" stroke-width="2"><circle cx="12" cy="12" r="10"/><path d="M2 12h20M12 2c3 3 3 17 0 20M12 2c-3 3-3 17 0 20"/></svg>
          www.vessolinhairstudio.example
        </li>
        <li>
          <span class="contact__dot"></span>
          @vessolinhairstudio
        </li>
      </ul>
      <p class="address">41782 Pelham Crest Rd, Larkmoor OH</p>
    </div>
  </section>
</main>
</body>
</html>
```